Psychotherapy, Life Coaching, Writer, Motivational Speaker

I am a psychotherapist, life coach, writer and speaker on health and wellness issues. I am a humanist - who believes that we are born to self-actualize - but life - changes that course. That we develop armor and coping mechanisms that divert our growth. I help people examine their road blocks to happiness. My business is unique in that I do concierge therapy. I work intensively - with multi-day sessions, I work internationally through tele-therapy - and traditionally - in an office space. My work is tailored to your needs.

Target Market(s)

Broad

Industry/Entity Type

Health

Contact Information for Business Card

Listen And Grow
Sam Perriton
248 East 39th Street
New York, NY 10027
(305) 555-0173

Requirements
Must have
• Clean lines... not too busy...
• FB page listing: Listen And Grow
• my Web page: www.listenandgrow-example.com
Nice to have
• I would love to be able to list the services: Psychotherapist, Life Coach, Motivational Speaker and Writer - but also don't want a crazy crowded card. Feel free to use the back for description.
Should not have
• Stay away from corny imagery - lotus flowers, zen, lily pond, clouds.

```html
<!DOCTYPE html>
<html lang="en">
<head>
<meta charset="utf-8">
<title>Listen And Grow – Business Card</title>
<link rel="stylesheet" href="https://fonts.googleapis.com/css2?family=Lato:wght@400;700&display=swap">
<style>
  :root {
    --backdrop: #ececed;
    --card-white: #ffffff;
    --brand-blue: #3e6ba7;
    --band-blue: #4c77b0;
    --back-blue-light: #5f8bc4;
    --back-blue-dark: #3b67a6;
    --ink: #1d1f24;
    --ink-soft: #2a2e38;
    --divider: #2b2d33;
  }
  * { margin: 0; padding: 0; box-sizing: border-box; }
  html, body {
    width: 1200px; height: 720px; overflow: hidden;
    background: var(--backdrop);
    font-family: "Lato", Arial, sans-serif;
  }
  .canvas { position: relative; width: 1200px; height: 720px; }

  .card {
    position: absolute; top: 241px; width: 420px; height: 239px;
    overflow: hidden;
  }
  .card--front { left: 147px; background: var(--card-white); }
  .card--back {
    left: 633px;
    background: linear-gradient(135deg, var(--back-blue-light), var(--back-blue-dark));
  }

  /* Front */
  .brand-title {
    position: absolute; right: 239px; top: 80px;
    text-align: right; color: var(--brand-blue);
    font-weight: 700; font-size: 31px; line-height: 36px;
  }
  .divider {
    position: absolute; left: 192px; top: 50px; width: 2px; height: 138px;
    background: linear-gradient(to bottom, rgba(43,45,51,0), var(--divider) 20%, var(--divider) 80%, rgba(43,45,51,0));
  }
  .details { position: absolute; left: 201px; top: 56px; color: var(--ink); }
  .person-name { font-size: 17px; line-height: 20px; color: var(--brand-blue); font-weight: 700; }
  .person-name .credentials { font-size: 14px; color: var(--ink); font-weight: 400; }
  .person-role { font-size: 13px; line-height: 17px; }
  .contact-list { list-style: none; margin-top: 5px; }
  .contact-list li {
    display: flex; align-items: center; gap: 4px;
    font-size: 13.5px; line-height: 16.5px; color: var(--ink-soft);
  }
  .contact-list svg { width: 11px; height: 11px; fill: var(--brand-blue); flex: none; }
  .address { margin-top: 4px; margin-left: 4px; font-size: 12.5px; line-height: 14px; }

  .social-band {
    position: absolute; left: 0; bottom: 0; width: 100%; height: 31px;
    background: var(--band-blue);
    display: flex; align-items: center; justify-content: center; gap: 4px;
    font-size: 14px; color: var(--ink);
  }
  .social-band .social-square { width: 10px; height: 10px; background: var(--card-white); }

  /* Back */
  .back-title {
    position: absolute; left: 32px; top: 58px;
    font-size: 20px; font-weight: 700; color: var(--ink);
  }
  .services {
    position: absolute; left: 32px; top: 97px;
    font-size: 13px; line-height: 16px; color: var(--ink-soft);
  }
  .appointment {
    position: absolute; left: 35px; top: 165px;
    font-size: 13px; color: var(--ink);
  }
</style>
</head>
<body>
<div class="canvas">

  <section class="card card--front">
    <h1 class="brand-title">Listen And<br>Grow</h1>
    <div class="divider"></div>
    <div class="details">
      <p class="person-name">Sam Perriton, <span class="credentials">LMHC, NCC</span></p>
      <p class="person-role">Psychotherapist.</p>
      <ul class="contact-list">
        <li>
          <svg viewBox="0 0 12 12" aria-hidden="true"><path d="M1 4c0-2 2-3 5-3s5 1 5 3v1H8V4H4v1H1zM3 6h6l2 5H1z"/></svg>
          (305) 555-0173
        </li>
        <li>
          <svg viewBox="0 0 12 12" aria-hidden="true"><path d="M0 2h12v8H0zM1 3l5 4 5-4v-.2H1z" fill-rule="evenodd"/></svg>
          sperriton@listenandgrow-example.com
        </li>
        <li>
          <svg viewBox="0 0 12 12" aria-hidden="true"><path d="M6 0a6 6 0 1 0 0 12A6 6 0 0 0 6 0zm0 1c.8.9 1.4 2.4 1.6 4.5H4.4C4.6 3.4 5.2 1.9 6 1zM1 5.5a5 5 0 0 1 2.4-3.8 9 9 0 0 0-.9 3.8zm7.6-3.8A5 5 0 0 1 11 5.5H9.5a9 9 0 0 0-.9-3.8zM1 6.5h1.5a9 9 0 0 0 .9 3.8A5 5 0 0 1 1 6.5zm3.4 0h3.2C7.4 8.6 6.8 10.1 6 11c-.8-.9-1.4-2.4-1.6-4.5zm5.1 0H11a5 5 0 0 1-2.4 3.8 9 9 0 0 0 .9-3.8z"/></svg>
          www.listenandgrow-example.com
        </li>
      </ul>
      <p class="address">248 East 39th Street<br>New York, NY 10027</p>
    </div>
    <div class="social-band">
      <span class="social-square"></span>
      <span>Listen And Grow</span>
    </div>
  </section>

  <section class="card card--back">
    <h2 class="back-title">Listen And Grow</h2>
    <p class="services">Psychotherapy,<br>Coaching,<br>Wellness Media</p>
    <p class="appointment">Your Next Appoinment is at...................... at.............. am/pm</p>
  </section>

</div>
</body>
</html>
```